Home page design for my business

My business will be selling templated drive-in movie theater websites. I would like my business to state to my customers that they get a free website (with hosting fees) where they can take ticket sales digitally. My company will be called Reel-Lanternworks (for Drive In Movie Theatres).

Here are some websites of my potential customers:
https://www.pelorcrest.example/
https://moonglowcinemas.example/
https://oakridgeoutdoorscreen.example/

```html
<!DOCTYPE html>
<html lang="en">
<head>
<meta charset="utf-8">
<title>Reel-Lanternworks — Free Websites for Drive-In Movie Theatres</title>
<link href="https://fonts.googleapis.com/css2?family=Kanit:ital,wght@1,800&family=Lato:wght@400;700&display=swap" rel="stylesheet">
<style>
:root{
  --navy:#0d3a8e;
  --red:#8a0a22;
  --ink:#1c1c1c;
  --muted:#3a3a3a;
  --white:#ffffff;
  --footer:#0b0b0d;
  --line:#c9c9cf;
}
*{box-sizing:border-box;margin:0;padding:0}
html,body{width:1200px;height:3731px;overflow:hidden}
body{position:relative;font-family:'Lato',sans-serif;color:var(--ink);background:var(--white)}
.abs{position:absolute}
.display{font-family:'Kanit',sans-serif;font-style:italic;font-weight:800;text-transform:uppercase;letter-spacing:-0.5px}
.btn{position:absolute;display:flex;align-items:center;justify-content:center;font-family:'Kanit',sans-serif;font-style:italic;font-weight:800;font-size:13px;text-transform:uppercase;color:var(--white);text-decoration:none;background:linear-gradient(90deg,var(--red),var(--navy))}

/* hero */
.hero{left:0;top:0;width:1200px;height:640px;background:linear-gradient(180deg,#6a4c94 0%,#9a6c8c 18%,#c58a6a 30%,#4f5e38 45%,#354a26 65%,#5d5a3e 80%,#2f3d22 100%)}
.hero-shade{left:0;top:0;width:1200px;height:640px;background:rgba(10,10,20,.22)}
.tagline{left:177px;top:16px;font-size:19px;color:var(--white)}
.socials{display:flex;gap:9px}
.social{width:28px;height:28px;border-radius:50%;border:2px solid var(--white);background:rgba(255,255,255,.15)}
.nav{left:132px;top:55px;width:936px;height:74px;background:var(--white);border-radius:6px}
.nav a{position:absolute;top:28px;font-size:13px;font-weight:700;color:#111;text-decoration:none;text-transform:uppercase}
.nav a.active{color:var(--red)}
.brand-tab{left:526px;top:18px;width:148px;height:110px;background:var(--white);border-radius:74px 74px 6px 6px;display:flex;align-items:center;justify-content:center}
.brand-name{font-family:'Kanit',sans-serif;font-style:italic;font-weight:800;font-size:15px;color:var(--navy);text-align:center;line-height:1.1}
.hero-title{left:0;width:1200px;top:242px;text-align:center;font-size:52px;line-height:60px;color:var(--white)}
.hero-copy{left:203px;width:794px;top:381px;text-align:center;font-size:13px;line-height:24px;color:var(--white)}

/* digital ticket */
.photo-frame{left:123px;top:736px;width:361px;height:362px;background:var(--white);box-shadow:0 6px 22px rgba(0,0,0,.18);padding:5px}
.photo-frame div{width:100%;height:100%;background:linear-gradient(135deg,#d8b678,#a9874f 60%,#6d5634)}
.photo-small{left:394px;top:977px;width:145px;height:143px;border:3px solid var(--white);background:linear-gradient(180deg,#3f6da6 0 14%,#e6e7ea 14% 70%,#3a3f3a 70%)}
.h2{font-size:32px;color:var(--navy)}
.rule{height:2px;background:var(--navy)}
.ticket-copy{left:610px;top:785px;width:470px;font-size:13px;line-height:24px;text-align:justify;color:var(--muted)}

/* fun night */
.fun{left:0;top:1217px;width:1200px;height:597px;background:linear-gradient(100deg,#7c0d27 0%,#5a1848 45%,#243a8a 80%,#1e3b8e 100%)}
.poster{top:1375px;width:226px;height:246px}
.poster-label{top:1632px;width:226px;text-align:center;font-size:14px;color:var(--white)}

/* rental */
.rental-img{top:1963px;width:302px;height:206px}
.caption{top:2185px;width:302px;text-align:center;font-size:14px;line-height:20px;color:#111}
.arrow{top:2037px;width:42px;height:42px;border-radius:50%;background:var(--white);box-shadow:0 2px 10px rgba(0,0,0,.22);display:flex;align-items:center;justify-content:center}

/* trailer */
.trailer{left:0;top:2304px;width:1200px;height:429px;background:radial-gradient(ellipse at 50% 55%,#5a4438 0%,#2b2424 45%,#121416 100%)}

/* contact */
.info-icon{width:52px;height:52px;border-radius:50%;background:linear-gradient(180deg,var(--navy),var(--red));display:flex;align-items:center;justify-content:center}
.info-title{font-size:16px;color:var(--navy)}
.info-text{font-size:14px;line-height:28px;color:#222}
.field{left:658px;width:352px;border:1px solid var(--line);border-radius:6px;font-size:12px;color:#666;padding:0 12px;display:flex;align-items:center}
.field.area{align-items:flex-start;padding-top:16px}

/* footer */
.footer{left:0;top:3369px;width:1200px;height:362px;background:var(--footer)}
.f-head{font-size:15px;color:var(--white)}
.f-list{list-style:none;font-size:12.5px;color:var(--white);line-height:28px}
.f-contact{font-size:12.5px;color:var(--white);line-height:21px}
.f-icon{width:26px;height:26px;border-radius:50%;background:linear-gradient(180deg,var(--navy),var(--red));display:flex;align-items:center;justify-content:center}
.f-social{width:34px;height:34px;border-radius:50%;border:2px solid var(--white)}
.copyright{left:0;width:1200px;top:3683px;text-align:center;font-size:13px;color:var(--white)}
</style>
</head>
<body>

<!-- Hero -->
<section>
  <div class="abs hero" role="img" aria-label="Aerial view of a drive-in lot with parked cars among trees at sunset"></div>
  <div class="abs hero-shade"></div>
  <div class="abs display tagline">Free site + hosting</div>
  <div class="abs socials" style="left:887px;top:14px">
    <span class="social" aria-label="Social link"></span>
    <span class="social" aria-label="Social link"></span>
    <span class="social" aria-label="Social link"></span>
    <span class="social" aria-label="Social link"></span>
  </div>
  <nav class="abs nav">
    <a class="active" style="left:46px">Home</a>
    <a style="left:127px">Food Menu</a>
    <a style="left:249px">FAQ</a>
    <a style="left:581px">Theater Rules</a>
    <a style="left:723px">Photos</a>
    <a style="left:817px">Contact Us</a>
  </nav>
  <div class="abs brand-tab"><span class="brand-name">Reel-<br>Lanternworks</span></div>
  <h1 class="abs display hero-title">A free website for<br>your drive-in theatre</h1>
  <p class="abs hero-copy">Reel-Lanternworks gives drive-in movie theatres a ready-made website for free, with hosting included. Sell tickets digitally, post showtimes and menus, and welcome more cars every night.</p>
  <a class="btn" style="left:522px;top:451px;width:156px;height:45px">Get Your Site</a>
</section>

<!-- Digital ticket -->
<section>
  <div class="abs photo-frame"><div role="img" aria-label="Hand holding a phone showing a digital movie ticket"></div></div>
  <div class="abs photo-small" role="img" aria-label="Drive-in movie screen"></div>
  <h2 class="abs display h2" style="left:610px;top:714px">Digital Ticket Sales</h2>
  <div class="abs rule" style="left:610px;top:764px;width:75px"></div>
  <p class="abs ticket-copy">Every Reel-Lanternworks website comes with digital ticket sales built in, so your guests can buy their spot before they ever reach the gate. Your site is free, and hosting is included, so there is nothing to install and no server to manage. Pick a template made for drive-in movie theatres, add your name, colours and photos, and you are ready to open the box office online. Guests choose a showing, pay on their phone and receive a ticket they can scan at the entrance. You see every sale as it happens, know how many cars to expect and spend less time handling cash at the booth. Update showtimes, prices, food menus and theater rules whenever you like from one simple dashboard. When a movie sells out, the site tells your guests right away. Let us handle the website so you can focus on the movies, the snacks and the stars overhead.</p>
  <a class="btn" style="left:610px;top:1090px;width:157px;height:43px">Start Selling</a>
</section>

<!-- Fun night -->
<section>
  <div class="abs fun"></div>
  <h2 class="abs display" style="left:0;width:1200px;top:1285px;text-align:center;font-size:30px;color:var(--white)">A fun night out for everyone</h2>
  <div class="abs poster" style="left:132px;background:linear-gradient(180deg,#efe6d4 0 30%,#b8281c 30% 90%,#efe6d4 90%)" role="img" aria-label="Sci-fi movie poster"></div>
  <div class="abs poster" style="left:368px;background:linear-gradient(180deg,#2a2018,#4a3424 70%,#c9a76a)" role="img" aria-label="Space movie poster"></div>
  <div class="abs poster" style="left:604px;background:linear-gradient(180deg,#c8241c 0 28%,#1d2840 28%)" role="img" aria-label="Retro sci-fi comic cover"></div>
  <div class="abs poster" style="left:840px;background:linear-gradient(180deg,#d9291c 0 32%,#f2d64a 32%)" role="img" aria-label="Superhero comic magazine cover"></div>
  <div class="abs display poster-label" style="left:132px">Lorem ipsum dolor</div>
  <div class="abs display poster-label" style="left:368px">Lorem ipsum dolor</div>
  <div class="abs display poster-label" style="left:604px">Lorem ipsum dolor</div>
  <div class="abs display poster-label" style="left:840px">Lorem ipsum dolor</div>
  <a class="btn" style="left:522px;top:1694px;width:156px;height:43px;background:var(--white);color:var(--navy)">Book Ticket</a>
</section>

<!-- Rental -->
<section>
  <h2 class="abs display h2" style="left:0;width:1200px;top:1888px;text-align:center;font-size:31px">Our Rental</h2>
  <div class="abs rule" style="left:564px;top:1939px;width:72px"></div>
  <div class="abs rental-img" style="left:133px;background:linear-gradient(180deg,#214a8a 0 12%,#a9adb3 12% 78%,#3a3c40 78%)" role="img" aria-label="Indoor lit rental screen"></div>
  <div class="abs rental-img" style="left:449px;background:linear-gradient(180deg,#3d5a2a 0 30%,#7c8a4e 30% 75%,#4a6a2e 75%)" role="img" aria-label="Aerial view of a drive-in screen field"></div>
  <div class="abs rental-img" style="left:763px;background:linear-gradient(180deg,#c9ccd0 0 35%,#2a2c30 35% 70%,#6a6e74 70%)" role="img" aria-label="Large outdoor screen in a parking lot"></div>
  <div class="abs display caption" style="left:133px">45 to 65 feet wide and as<br>tall as 30 feet</div>
  <div class="abs display caption" style="left:449px">55 to 75 feet wide and as<br>tall as 35 feet</div>
  <div class="abs display caption" style="left:763px">65 to 85 feet wide and as<br>tall as 40 feet</div>
  <div class="abs arrow" style="left:111px"><svg width="12" height="14" viewBox="0 0 12 14"><path d="M8 2 3 7l5 5" fill="none" stroke="#222" stroke-width="2"/></svg></div>
  <div class="abs arrow" style="left:1045px"><svg width="12" height="14" viewBox="0 0 12 14"><path d="M4 2l5 5-5 5" fill="none" stroke="#222" stroke-width="2"/></svg></div>
</section>

<!-- Trailer -->
<section>
  <div class="abs trailer" role="img" aria-label="Dark still from an upcoming horror trailer"></div>
  <h2 class="abs display" style="left:0;width:1200px;top:2376px;text-align:center;font-size:30px;color:var(--white)">Upcoming Trailer</h2>
  <div class="abs rule" style="left:563px;top:2424px;width:74px;background:var(--white)"></div>
  <svg class="abs" style="left:580px;top:2499px" width="40" height="40" viewBox="0 0 40 40"><circle cx="20" cy="20" r="19" fill="#fff"/><path d="M16 12l12 8-12 8z" fill="#111"/></svg>
</section>

<!-- Contact -->
<section>
  <h2 class="abs display h2" style="left:199px;top:2830px">Contact Us</h2>
  <div class="abs info-icon" style="left:204px;top:2926px"><svg width="16" height="20" viewBox="0 0 16 20"><path d="M8 1a6 6 0 0 0-6 6c0 5 6 12 6 12s6-7 6-12a6 6 0 0 0-6-6z" fill="#fff"/><circle cx="8" cy="7" r="2.3" fill="#3a2a6a"/></svg></div>
  <div class="abs display info-title" style="left:268px;top:2922px">Location</div>
  <div class="abs info-text" style="left:268px;top:2952px">123 Lorem ipsum dolor sit amet<br>consectetur adipiscing elit.</div>
  <div class="abs info-icon" style="left:204px;top:3046px"><svg width="18" height="14" viewBox="0 0 18 14"><rect x="1" y="1" width="16" height="12" rx="1" fill="#fff"/><path d="M1 2l8 6 8-6" fill="none" stroke="#3a2a6a" stroke-width="1.5"/></svg></div>
  <div class="abs display info-title" style="left:268px;top:3043px">Email Address</div>
  <div class="abs info-text" style="left:268px;top:3074px">hello@reel-lanternworks.example</div>
  <div class="abs info-icon" style="left:204px;top:3141px"><svg width="18" height="18" viewBox="0 0 18 18"><path d="M4 1l3 4-2 2c1 3 3 5 6 6l2-2 4 3-2 3C8 17 1 10 1 3z" fill="#fff"/></svg></div>
  <div class="abs display info-title" style="left:268px;top:3139px">Phone Number</div>
  <div class="abs info-text" style="left:268px;top:3170px">+1 888 888 8888</div>

  <h2 class="abs display h2" style="left:656px;top:2830px">Get in Touch</h2>
  <div class="abs field" style="top:2899px;height:48px">Full Name</div>
  <div class="abs field" style="top:2963px;height:48px">Email address</div>
  <div class="abs field" style="top:3027px;height:48px">Phone Number</div>
  <div class="abs field area" style="top:3091px;height:121px">Message</div>
  <a class="btn" style="left:658px;top:3239px;width:352px;height:45px;background:linear-gradient(180deg,var(--navy),var(--red))">Submit</a>
</section>

<!-- Footer -->
<footer>
  <div class="abs footer"></div>
  <div class="abs display f-head" style="left:132px;top:3446px">Quick Links</div>
  <ul class="abs f-list" style="left:133px;top:3480px"><li>Home</li><li>Food Menu</li><li>Theater Rules</li><li>Photos</li></ul>
  <div class="abs display f-head" style="left:339px;top:3446px">Legal</div>
  <ul class="abs f-list" style="left:334px;top:3480px"><li>Terms &amp; Conditions</li><li>Privacy Policy</li><li>FAQ</li><li>Contact Us</li></ul>
  <div class="abs display f-head" style="left:529px;top:3446px">Contact Us</div>
  <div class="abs f-icon" style="left:529px;top:3484px"><svg width="10" height="13" viewBox="0 0 16 20"><path d="M8 1a6 6 0 0 0-6 6c0 5 6 12 6 12s6-7 6-12a6 6 0 0 0-6-6z" fill="#fff"/></svg></div>
  <div class="abs f-contact" style="left:570px;top:3482px">123 Sed ut perspiciatis unde omnis is<br>te natus error sit voluptatem</div>
  <div class="abs f-icon" style="left:529px;top:3541px"><svg width="12" height="10" viewBox="0 0 18 14"><rect x="1" y="1" width="16" height="12" fill="#fff"/></svg></div>
  <div class="abs f-contact" style="left:570px;top:3543px">hello@reel-lanternworks.example</div>
  <div class="abs f-icon" style="left:529px;top:3582px"><svg width="12" height="12" viewBox="0 0 18 18"><path d="M4 1l3 4-2 2c1 3 3 5 6 6l2-2 4 3-2 3C8 17 1 10 1 3z" fill="#fff"/></svg></div>
  <div class="abs f-contact" style="left:570px;top:3584px">+1 888 888 8888</div>
  <div class="abs brand-name" style="left:848px;top:3478px;width:240px;font-size:26px;color:var(--white)">Reel-Lanternworks</div>
  <div class="abs" style="left:880px;top:3578px;display:flex;gap:11px">
    <span class="f-social" aria-label="Social link"></span>
    <span class="f-social" aria-label="Social link"></span>
    <span class="f-social" aria-label="Social link"></span>
    <span class="f-social" aria-label="Social link"></span>
  </div>
  <div class="abs copyright">© 2022 Reel-Lanternworks. | All Rights Reserved</div>
</footer>

</body>
</html>
```